I need new business cards designed

I would like to get some new designs on business cards. I will upload my logo for reference. The business cards that were designed for me a few months ago were too difficult for the print companies to work with. My company is Quillbrook.net LLC. It is an art company that sells painting and expression cards online.

```html
<!DOCTYPE html>
<html lang="en">
<head>
<meta charset="utf-8">
<title>Quillbrook.net – Business Cards</title>
<link href="https://fonts.googleapis.com/css2?family=Open+Sans:wght@400;600;700&display=swap" rel="stylesheet">
<style>
  :root{
    --bg:#cfcecb;
    --card:#ffffff;
    --brand-blue:#0aa0dc;
    --brand-navy:#363a7c;
    --text-dark:#1f1f24;
    --edge:#0aa0dc;
  }
  *{box-sizing:border-box;margin:0;padding:0}
  html,body{width:1200px;height:801px;overflow:hidden}
  body{background:var(--bg);font-family:"Open Sans",Arial,sans-serif;position:relative}
  .card{
    position:absolute;width:540px;height:309px;background:var(--card);
    border-radius:16px;border-bottom:4px solid var(--edge);
    box-shadow:0 14px 28px rgba(0,0,0,.22);overflow:hidden;
  }
  .card--front{left:40px;top:246px}
  .card--back{left:620px;top:246px}

  /* front */
  .front-brand{position:absolute;left:36px;top:120px;display:flex;align-items:center;gap:12px}
  .brand-square{width:44px;height:44px;background:var(--brand-blue)}
  .brand-name{font-size:25px;font-weight:600;color:var(--brand-navy);line-height:1}
  .brand-tagline{font-size:11px;color:var(--brand-navy);margin-top:5px;letter-spacing:.4px}
  .divider{position:absolute;left:300px;top:40px;width:2px;height:226px;background:var(--brand-blue)}
  .contact{position:absolute;left:318px;top:46px;color:var(--text-dark)}
  .contact-name{font-size:21px;font-weight:700;color:var(--brand-blue);letter-spacing:.5px}
  .contact-role{font-size:13px;margin-bottom:10px}
  .contact-line{font-size:12.5px;line-height:19px}
  .contact-list{list-style:none;margin-top:10px}
  .contact-list li{display:flex;align-items:center;gap:7px;font-size:12.5px;line-height:21px}
  .contact-list svg{width:12px;height:12px;fill:var(--brand-blue)}
  .social{position:absolute;left:36px;bottom:24px;display:flex;gap:10px}
  .social span{width:14px;height:14px;border-radius:50%;background:var(--brand-blue)}

  /* back */
  .back-square{position:absolute;left:40px;top:88px;width:120px;height:120px;background:var(--brand-blue)}
  .back-brand{position:absolute;left:184px;top:116px}
  .back-brand .brand-name{font-size:44px}
  .back-brand .brand-tagline{font-size:17px;margin-top:8px}
</style>
</head>
<body>
  <section class="card card--front" aria-label="Business card front">
    <div class="front-brand">
      <div class="brand-square"></div>
      <div>
        <div class="brand-name">Quillbrook.net</div>
        <div class="brand-tagline">Paint · Express · Share</div>
      </div>
    </div>
    <div class="divider"></div>
    <div class="contact">
      <div class="contact-name">NORA WHITFIELD</div>
      <div class="contact-role">Managing Director</div>
      <div class="contact-line">Your address, City</div>
      <div class="contact-line">State, Zip 1234</div>
      <ul class="contact-list">
        <li><svg viewBox="0 0 24 24"><path d="M6.6 10.8a15 15 0 0 0 6.6 6.6l2.2-2.2a1 1 0 0 1 1-.25 11.4 11.4 0 0 0 3.6.57 1 1 0 0 1 1 1V20a1 1 0 0 1-1 1A17 17 0 0 1 3 4a1 1 0 0 1 1-1h3.5a1 1 0 0 1 1 1c0 1.25.2 2.45.57 3.6a1 1 0 0 1-.25 1z"/></svg>123-456-7890</li>
        <li><svg viewBox="0 0 24 24"><path d="M2 5h20v14H2z M2 5l10 8 10-8" /></svg>hello@quillbrook.net</li>
        <li><svg viewBox="0 0 24 24"><circle cx="12" cy="12" r="10"/></svg>www.Quillbrook.net</li>
      </ul>
    </div>
    <div class="social" aria-label="Social links"><span></span><span></span><span></span></div>
  </section>

  <section class="card card--back" aria-label="Business card back">
    <div class="back-square"></div>
    <div class="back-brand">
      <div class="brand-name">Quillbrook.net</div>
      <div class="brand-tagline">Paint · Express · Share</div>
    </div>
  </section>
</body>
</html>
```